Kellwyn Surface Records

I have a current web site that it looking quite aged and it needs a new lease of life. This is a Graffiti Management Website so is all about data processing and management of information. I want a html 5 view on any platform design. clean crisp and new. I have provided some screen shots of my current site.

Target Market(s)

The Target Market will be local government. most users will not be heavy pc users

Industry/Entity Type

Management

Font styles to use
Sans Serif
Other font styles liked:
• web font like calibri

Colors

Designer to choose colors to be used in the design.

Requirements
Must have
• Must have menus similar to attachments

```html
<!DOCTYPE html>
<html lang="en">
<head>
<meta charset="utf-8">
<title>Kellwyn Surface Records</title>
<link rel="stylesheet" href="https://fonts.googleapis.com/css2?family=Oswald:wght@400;500&family=Open+Sans:wght@400;600&family=Roboto:wght@400&display=swap">
<style>
:root{
  --sky:#4aa3d8;
  --sky-dark:#2f86c2;
  --navy:#0a1f7a;
  --ink:#333;
  --muted:#777;
  --rule:#e4e4e4;
  --night:#1c2536;
  --footer:#111;
  --white:#fff;
}
*{margin:0;padding:0;box-sizing:border-box}
html,body{width:825px;height:1200px;overflow:hidden;background:var(--white)}
body{position:relative;font-family:"Open Sans",sans-serif;color:var(--ink)}
.abs{position:absolute}

.topbar{left:0;top:0;width:825px;height:44px;background:repeating-linear-gradient(180deg,#5fb0e4 0 2px,#4d9fd8 2px 4px)}
.brand{left:120px;top:4px;font-family:"Oswald",sans-serif;font-size:30px;font-weight:500;letter-spacing:22px;color:var(--white);line-height:36px}
.connect{left:555px;top:15px;font-size:9px;color:var(--white);font-weight:600}
.social-dot{width:9px;height:9px;border-radius:50%;background:var(--white);top:17px}
.tagband{left:0;top:44px;width:825px;height:12px;background:var(--navy);border-bottom:2px solid var(--sky)}
.tagline{left:119px;top:44px;font-size:9px;font-weight:600;letter-spacing:1.3px;color:var(--white);line-height:12px;text-transform:uppercase}

.nav{left:0;top:58px;width:825px;height:37px;border-bottom:1px solid var(--rule);display:flex;align-items:center;padding-left:118px;font-size:10px;color:#444}
.nav span{padding:0 18px;border-left:1px solid var(--rule);line-height:14px}
.nav span:first-child{padding-left:0;border-left:none;color:var(--sky)}

.hero{left:0;top:95px;width:825px;height:336px;background:radial-gradient(ellipse at 45% 45%,#8a8a8a,#5a5a5a 70%,#454545)}
.hero-title{left:478px;top:208px;font-family:"Oswald",sans-serif;font-weight:500;color:var(--white);text-shadow:1px 1px 2px #000;line-height:1}
.hero-title .big{font-size:34px;display:block}
.hero-title .sub{font-size:28px;display:block;margin-top:8px}
.arrow-btn{width:24px;height:24px;border-radius:50%;background:#1a1a1a;top:302px}

.welcome{left:0;top:446px;width:825px;text-align:center;font-family:"Oswald",sans-serif;font-weight:400;font-size:24px;color:#444}
.welcome em{font-style:normal;color:var(--sky)}
.intro{left:118px;top:487px;width:590px;text-align:center;font-size:7.4px;line-height:13.5px;color:var(--muted)}

.feature-box{left:320px;top:548px;width:183px;height:204px;background:#f8f8f8;border:1px solid #eee}
.feature{width:180px;text-align:center}
.feature .icon{width:76px;height:76px;margin:0 auto;border-radius:50%;background:var(--sky);border:3px solid #cfe6f4}
.feature .shadow{width:60px;height:4px;margin:10px auto 0;border-radius:50%;background:radial-gradient(#ddd,transparent 70%)}
.feature h3{font-size:14px;font-weight:400;color:#333;margin-top:12px}
.feature p{font-size:7.2px;line-height:14px;color:var(--muted);margin:6px auto 0;width:166px}

.clients{left:0;top:775px;width:825px;height:158px;background:linear-gradient(180deg,#242f45,#1a2233 60%,#2b3040)}
.clients h2{position:absolute;left:0;top:18px;width:825px;text-align:center;font-family:"Roboto",sans-serif;font-weight:400;font-size:15px;color:var(--white)}
.quote{left:155px;top:843px;width:515px;text-align:center;font-family:"Roboto",sans-serif;font-size:12.4px;line-height:19px;color:var(--white)}
.author{left:0;top:885px;width:825px;text-align:center;font-size:9px;color:#dde}
.qmark{font-family:"Oswald",sans-serif;font-size:22px;color:var(--white);line-height:1}
.clients .line{position:absolute;left:118px;top:142px;width:590px;height:1px;background:#3b4558}

.stats-tag{left:118px;top:957px;width:149px;height:27px;background:var(--sky);color:var(--white);font-size:14.5px;font-weight:600;line-height:27px;padding-left:10px}
.stats-copy{left:118px;top:994px;width:280px;font-size:7.8px;line-height:14.5px;color:#555}
.stats-copy p+p{margin-top:9px}
.chart{left:440px;top:950px}

.footer{left:0;top:1127px;width:825px;height:73px;background:var(--footer)}
.copy{left:119px;top:1145px;font-size:7.6px;color:#aaa}
.footlinks{left:119px;top:1169px;font-size:7.2px;color:#aaa}
.fsocial{width:18px;height:18px;border-radius:50%;border:1px solid #555;top:1155px}
.news-label{left:520px;top:1140px;font-size:8.6px;color:#ddd}
.news-input{left:521px;top:1161px;width:127px;height:20px;background:#2a2a2a;font-size:6px;color:#777;padding:7px 9px}
.news-btn{left:656px;top:1160px;width:53px;height:21px;background:var(--sky-dark);border-radius:2px;color:var(--white);font-size:8.6px;text-align:center;line-height:21px}
</style>
</head>
<body>

<header>
  <div class="abs topbar"></div>
  <div class="abs brand">KSR</div>
  <div class="abs connect">Connect With Us :</div>
  <div class="abs social-dot" style="left:638px"></div>
  <div class="abs social-dot" style="left:657px"></div>
  <div class="abs social-dot" style="left:679px"></div>
  <div class="abs social-dot" style="left:699px"></div>
  <div class="abs tagband"></div>
  <div class="abs tagline">Kellwyn Surface Records</div>
  <nav class="abs nav">
    <span>Home</span><span>About Us</span><span>Products</span><span>Reports</span><span>Benefits</span><span>Legislation</span><span>Demo Login</span><span>Contact Us</span>
  </nav>
</header>

<section>
  <div class="abs hero" role="img" aria-label="Businessman in a suit facing a hand-drawn rising line chart on a grey concrete wall"></div>
  <div class="abs hero-title"><span class="big">KSR</span><span class="sub">STATISTICAL REPORTS</span></div>
  <div class="abs arrow-btn" style="left:478px"></div>
  <div class="abs arrow-btn" style="left:508px"></div>
  <svg class="abs" style="left:478px;top:302px" width="60" height="24" viewBox="0 0 60 24">
    <path d="M14 7 L9 12 L14 17" fill="none" stroke="#fff" stroke-width="2"/>
    <path d="M42 7 L47 12 L42 17" fill="none" stroke="#fff" stroke-width="2"/>
  </svg>
</section>

<section>
  <h1 class="abs welcome">Welcome To <em>KSR</em></h1>
  <p class="abs intro">Lorem ipsum dolor sit amet, consectetur adipisicing elit, sed do eiusmod tempor incididunt ut labore et dolore magna aliqua. Ut enim ad minim veniam, quis nostrud exercitation ullamco laboris nisi ut aliquip ex ea commodo consequat. Duis aute irure dolor in reprehenderit in voluptate velit esse cillum dolore eu fugiat nulla pariatur. Excepteur sint occaecat cupidatat non proident, sunt in culpa qui officia deserunt mollit anim id est laborum</p>

  <div class="abs feature-box"></div>
  <div class="abs feature" style="left:121px;top:562px">
    <div class="icon"><svg width="70" height="70" viewBox="0 0 70 70"><g fill="#fff"><rect x="20" y="44" width="4" height="8"/><rect x="26" y="40" width="4" height="12"/><rect x="32" y="37" width="4" height="15"/><rect x="38" y="33" width="4" height="19"/><rect x="44" y="28" width="4" height="24"/></g><path d="M22 38 Q36 34 46 20" fill="none" stroke="#fff" stroke-width="3"/><path d="M42 18 L50 16 L48 24 Z" fill="#fff"/></svg></div>
    <div class="shadow"></div>
    <h3>Products</h3>
    <p>KSR provides a National Register of Vandalism and Graffiti. Subscribers to the KSR Database can Add, Change, Report on and Archive their own Graffiti Jobs.</p>
  </div>
  <div class="abs feature" style="left:322px;top:562px">
    <div class="icon"><svg width="70" height="70" viewBox="0 0 70 70"><rect x="20" y="21" width="30" height="24" fill="none" stroke="#fff" stroke-width="2.5"/><g fill="#fff"><rect x="25" y="34" width="4" height="8"/><rect x="31" y="30" width="4" height="12"/><rect x="37" y="32" width="4" height="10"/><rect x="43" y="27" width="4" height="15"/></g><path d="M32 47 L38 47 L35 51 Z" fill="#fff"/></svg></div>
    <div class="shadow"></div>
    <h3>Benefits</h3>
    <p>KSR provides a National Register of Vandalism and Graffiti. Subscribers to the KSR Database can Add, Change, Report on and Archive their own Graffiti Jobs.</p>
  </div>
  <div class="abs feature" style="left:526px;top:562px">
    <div class="icon"><svg width="70" height="70" viewBox="0 0 70 70"><circle cx="35" cy="35" r="16" fill="#fff"/><path d="M35 35 L35 19 M35 35 L51 35 M35 35 L24 46" stroke="#4aa3d8" stroke-width="2.5"/></svg></div>
    <div class="shadow"></div>
    <h3>Legislation</h3>
    <p>KSR provides a National Register of Vandalism and Graffiti. Subscribers to the KSR Database can Add, Change, Report on and Archive their own Graffiti Jobs.</p>
  </div>
</section>

<section class="abs clients" role="img" aria-label="Blurred night view of a city skyline">
  <h2>WHAT OUR CLIENTS SAY</h2>
  <div class="line"></div>
</section>
<div class="abs qmark" style="left:126px;top:850px">&#8220;</div>
<p class="abs quote">KSR is an Online Database System to Manage Graffiti in your area or Your Properties KSR allows you to Register, Track, Report and Archive Graffiti Jobs with Photographic Records.</p>
<div class="abs author">&ndash; Mara, Tellvane</div>
<div class="abs qmark" style="left:675px;top:878px">&#8221;</div>

<section>
  <div class="abs stats-tag">Statistical Reports</div>
  <div class="abs stats-copy">
    <p>Statistical Reports can be done instantaneously and can be run on any data stored with in KSR. Charts and Graphs are available to clearly show trends and details for Management Purposes.</p>
    <p>Comparison reports (both historically and geographically) can show the effectiveness of anti graffiti policy. Detail Reports can be run Monthly, Quarterly and Annually.</p>
  </div>
  <svg class="abs chart" width="280" height="155" viewBox="440 950 280 155" font-family="Open Sans, sans-serif">
    <g stroke="#ddd" stroke-width="1.5" fill="none">
      <rect x="471" y="959" width="237" height="128"/>
      <line x1="493" y1="959" x2="493" y2="1087"/><line x1="535" y1="959" x2="535" y2="1087"/>
      <line x1="578" y1="959" x2="578" y2="1087"/><line x1="621" y1="959" x2="621" y2="1087"/>
      <line x1="663" y1="959" x2="663" y2="1087"/>
      <line x1="471" y1="980" x2="708" y2="980"/><line x1="471" y1="1002" x2="708" y2="1002"/>
      <line x1="471" y1="1023" x2="708" y2="1023"/><line x1="471" y1="1045" x2="708" y2="1045"/>
      <line x1="471" y1="1066" x2="708" y2="1066"/>
    </g>
    <g font-size="6.5" fill="#333" text-anchor="end">
      <text x="468" y="982">30</text><text x="468" y="1004">25</text><text x="468" y="1025">20</text>
      <text x="468" y="1047">10</text><text x="468" y="1068">5</text>
    </g>
    <rect x="480" y="1074" width="24" height="12" fill="#c8e68a" stroke="#8cbf3f"/>
    <rect x="522" y="1054" width="25" height="32" fill="#a7def0" stroke="#5fbad8"/>
    <rect x="566" y="1010" width="24" height="76" fill="#f7b8cf" stroke="#e57aa0"/>
    <rect x="610" y="995" width="24" height="91" fill="#f9cc7a" stroke="#e9a53a"/>
    <rect x="653" y="988" width="24" height="98" fill="#f4a3a3" stroke="#e06666"/>
    <g font-size="6" fill="#444">
      <text x="484" y="1083">2.3 %</text>
      <text transform="translate(537 1072) rotate(-90)">6.2 %</text>
      <text transform="translate(580 1040) rotate(-90)">23.3 %</text>
      <text transform="translate(624 1024) rotate(-90)">25.4 %</text>
      <text transform="translate(667 1016) rotate(-90)">28.8 %</text>
    </g>
    <g font-size="8" fill="#333" text-anchor="middle">
      <text x="535" y="1101">Graffiti</text><text x="578" y="1101">Tag</text>
      <text x="621" y="1101">Throw Up</text><text x="668" y="1101">UnGraffiti</text>
    </g>
  </svg>
</section>

<footer>
  <div class="abs footer"></div>
  <div class="abs copy">&copy;2014 KSR , All Rights Reserved.</div>
  <div class="abs footlinks">Home&nbsp;|&nbsp; Reports &nbsp;|&nbsp; Benefits &nbsp;|&nbsp; Products &nbsp;|&nbsp; Legislation &nbsp;|&nbsp; Contact Us</div>
  <div class="abs fsocial" style="left:380px"></div>
  <div class="abs fsocial" style="left:403px"></div>
  <div class="abs fsocial" style="left:427px"></div>
  <div class="abs news-label">Newsletter Sign Up</div>
  <div class="abs news-input">Enter Your Email</div>
  <div class="abs news-btn">Subscribe</div>
</footer>

</body>
</html>
```